New Poster Design Project

Make an out standing A2 poster with below information,it is out first edition!Use the Attached image as background,Thanx!

Lindvik Kora Lights Gathering
16 - 22 June 2014
Www.klgmeet.example

Creating a new vision of Africa through African Arts and Culture

Guest speakers / Artists

Tandiwe Okoro-Lyngstad (S.A)
Tesfaye Birhanu Worku (Ethio)
Ronny Kato-Mbabazi (Uganda)
Håkon Løvli (Nor)
Velvet River Troupe (Zim)
Kalimbora Band (Moz,Nor,Swe & Zim)
Dj Koko Rae with Afro beats (Ghana/UK )
Dj Marlow/Silver Lynx with collage mix (Bergen)

@ Cafe Tumaini, Nordvik Global Heritage House (Nghh) Kraftverkshallen,Havnetorget,By Lunden & Fjellsmau gate

Mon-Thur
Free entry,food & drinks served

Fri - Entry by donation & Sat - Klgmeet closing ceremony (100kr)
Updates

Project Deadline Extended

Project Deadline Extended
Reason: I made a mistake on extending time on this project now I can not reverse the extended time aaarrrr!!!I really dont have time,The poster should be all over the place by now since Im left with a couple of days away to the festival!!!I need someone to QuickFix me a A2 top notch poster in No time...my deadline is NOW NOW,LATEST Wednesday 21 May 2014,Thanx!

Industry/Entity Type

Cafe

Requirements
Must have
• sponsors logo
Nice to have
• Symbols
Should not have

```html
<!DOCTYPE html>
<html lang="en">
<head>
<meta charset="utf-8">
<title>Lindvik Kora Lights Gathering</title>
<link href="https://fonts.googleapis.com/css2?family=Berkshire+Swash&family=Montserrat:wght@300;400;600&family=Varela+Round&family=Lustria&display=swap" rel="stylesheet">
<style>
  :root {
    --backdrop: #444645;
    --teal: #0ccf9f;
    --teal-bright: #1fd8a4;
    --ink: #1d1d1d;
    --navy: #1a2a86;
    --blue: #2a5bd6;
    --title-blue: #3a62d8;
    --black: #000;
    --orange: #f7941d;
    --pale: #dde7ff;
    --white: #fff;
    --grey: #8a8a8a;
  }
  * { margin: 0; padding: 0; box-sizing: border-box; }
  html, body { width: 1200px; height: 1029px; overflow: hidden; background: var(--backdrop); }
  .poster {
    position: absolute; left: 257px; top: 28px; width: 686px; height: 971px;
    font-family: "Montserrat", sans-serif; overflow: hidden;
  }
  .panel { position: absolute; }
  .panel--teal { left: 0; top: 0; width: 345px; height: 466px; background: var(--teal); }
  .panel--black { left: 345px; top: 0; width: 341px; height: 173px; background: var(--black); }
  .panel--blue { left: 0; top: 466px; width: 345px; height: 414px; background: var(--blue); }
  .photo {
    position: absolute; left: 345px; top: 173px; width: 341px; height: 707px;
    background: radial-gradient(ellipse at 60% 55%, #8a7560 0%, #4a3a2c 45%, #1c140f 100%);
  }
  .title {
    position: absolute; left: 80px; top: 12px;
    font-family: "Berkshire Swash", cursive; font-size: 112px; line-height: 1;
    color: var(--title-blue); font-weight: 400;
  }
  .subtitle {
    position: absolute; left: 488px; top: 56px;
    font-family: "Varela Round", sans-serif; font-size: 27px; line-height: 31px;
    color: var(--teal-bright);
  }
  .website { position: absolute; left: 90px; top: 134px; font-size: 14px; font-weight: 600; color: var(--navy); }
  .dates { position: absolute; left: 374px; top: 134px; font-size: 15px; font-weight: 600; color: var(--white); }
  .tagline { position: absolute; top: 166px; font-size: 16.5px; font-weight: 400; white-space: nowrap; }
  .tagline--left { right: 343px; color: var(--ink); }
  .tagline--right { left: 349px; color: var(--teal-bright); }
  .lineup { position: absolute; left: 30px; top: 236px; }
  .lineup__heading { font-family: "Lustria", serif; font-size: 20px; color: var(--ink); font-weight: 400; margin-bottom: 8px; }
  .lineup__list { list-style: none; padding-left: 4px; }
  .lineup__list li { font-size: 12.6px; line-height: 20.6px; color: var(--ink); font-weight: 400; white-space: nowrap; }
  .venue { position: absolute; left: 27px; top: 483px; width: 310px; color: var(--white); }
  .venue p { font-size: 16px; line-height: 24px; white-space: nowrap; }
  .venue .venue__street { font-size: 13.5px; line-height: 26px; }
  .rule { position: absolute; left: 19px; width: 251px; height: 1px; background: var(--teal); }
  .rule--one { top: 589px; }
  .rule--two { top: 700px; }
  .entry { position: absolute; left: 27px; font-size: 17px; line-height: 25.7px; font-weight: 600; }
  .entry--week { top: 608px; }
  .entry--weekend { top: 719px; color: var(--orange); }
  .entry__days { color: var(--orange); }
  .entry__note { color: var(--pale); }
  .sponsors { position: absolute; left: 0; top: 880px; width: 686px; height: 91px; background: var(--white); }
  .sponsors__label { position: absolute; top: 4px; width: 100%; text-align: center; font-size: 10px; color: var(--grey); }
  .sponsors__row {
    position: absolute; top: 28px; left: 8px; right: 8px; height: 52px;
    display: flex; justify-content: space-between; align-items: center;
  }
  .sponsor { display: flex; align-items: center; gap: 4px; font-size: 10.5px; font-weight: 600; color: var(--ink); white-space: nowrap; }
  .sponsor__mark { width: 12px; height: 12px; border-radius: 50%; background: var(--blue); }
  .sponsor__mark--square { border-radius: 0; background: var(--orange); }
</style>
</head>
<body>
<main class="poster">
  <div class="panel panel--teal"></div>
  <div class="panel panel--black"></div>
  <div class="photo" role="img" aria-label="Sepia portrait of a smiling performer in a white head wrap resting her arms on a carved kalimba"></div>
  <div class="panel panel--blue"></div>

  <h1 class="title">Lindvik</h1>
  <p class="subtitle">Kora Lights<br>Gathering</p>
  <p class="website">www.klgmeet.example</p>
  <p class="dates">16 - 22 June 2014</p>
  <p class="tagline tagline--left">Creating a new vision of Africa</p>
  <p class="tagline tagline--right">through African Arts and Culture</p>

  <section class="lineup">
    <h2 class="lineup__heading">Guest speakers / Artists</h2>
    <ul class="lineup__list">
      <li>Tandiwe Okoro-Lyngstad (S.A)</li>
      <li>Tesfaye Birhanu Worku (Ethio)</li>
      <li>Ronny Kato-Mbabazi (Uganda)</li>
      <li>Håkon Løvli (Nor)</li>
      <li>Velvet River Troupe (Zim)</li>
      <li>Kalimbora Band (Moz,Nor,Swe &amp; Zim)</li>
      <li>Dj Koko Rae with Afro beats (Ghana/UK )</li>
      <li>Dj Marlow/Silver Lynx with collage mix</li>
    </ul>
  </section>

  <section class="venue">
    <p>@ Cafe Tumaini, Nordvik Global</p>
    <p>Heritage House (Nghh)</p>
    <p>Kraftverkshallen,Havnetorget,</p>
    <p class="venue__street">By Lunden &amp; Fjellsmau gate</p>
  </section>
  <div class="rule rule--one"></div>
  <p class="entry entry--week">
    <span class="entry__days">MON-THUR</span><br>
    <span class="entry__note">Free entry,<br>food &amp; drinks served</span>
  </p>
  <div class="rule rule--two"></div>
  <p class="entry entry--weekend">FRI - Entry by donation<br>SAT - Klgmeet closing ceremony<br>(100kr)</p>

  <footer class="sponsors">
    <p class="sponsors__label">Supported by</p>
    <div class="sponsors__row">
      <span class="sponsor">KLG</span>
      <span class="sponsor"><span class="sponsor__mark sponsor__mark--square"></span>voltkjeller.example</span>
      <span class="sponsor">ungfond.example</span>
      <span class="sponsor"><span class="sponsor__mark"></span>Lindvik Kommune</span>
      <span class="sponsor">NGHH</span>
      <span class="sponsor">Sunu Dance Ensemble</span>
      <span class="sponsor">Friviljehuset</span>
    </div>
  </footer>
</main>
</body>
</html>
```